Verodex business card

Business card for sustainable investment company called "Verodex". Verodex is an exchange platform selling carbon credits between buyers and sellers. Carbon Credits are an environmental commodity for reducing global carbon emissions.

the card should obviously have our logo and the theme should be sustainability/environment mixed with a trading platform.

Contact Information for Business Card

Logo, Name, Title, Phone, Email

Colors
0054AA
0677BA
7BADD7
CADEEF
E8F1F8
0094D4
00A9DD
6FCCEA
C7EBF8
E9F6FB
00AB8E
00BBA5
67D7C9
C6EFE9
E9F9F6
59FF00
82FF00
B8FF75
E3FFCB
F4FFEA

```html
<!DOCTYPE html>
<html lang="en">
<head>
<meta charset="utf-8">
<title>Verodex business card</title>
<link href="https://fonts.googleapis.com/css2?family=Montserrat:wght@600;700;800&family=Open+Sans:wght@400;600&display=swap" rel="stylesheet">
<style>
  :root {
    --stage: #e9edf2;
    --navy: #142a4f;
    --navy-deep: #0d1d38;
    --emboss: #0a1326;
    --white: #ffffff;
    --sky: #5aa6dd;
    --cyan: #62c8dc;
    --blue: #4a80c6;
  }
  * { box-sizing: border-box; margin: 0; padding: 0; }
  html, body { width: 1200px; height: 780px; overflow: hidden; background: var(--stage); }
  .stage {
    width: 1200px; height: 780px;
    display: flex; align-items: center; justify-content: center; gap: 40px;
  }
  .card {
    position: relative; width: 540px; height: 310px;
    border-radius: 22px; overflow: hidden; background: var(--navy);
    box-shadow: 0 10px 24px rgba(13, 29, 56, 0.25);
  }
  .card-art { position: absolute; inset: 0; }

  /* back side */
  .back-brand {
    position: absolute; left: 0; right: 0; top: 0; bottom: 0;
    display: flex; align-items: center; justify-content: center; gap: 16px;
  }
  .back-brand .brand-mark { width: 38px; height: 38px; background: var(--emboss); }
  .back-brand .brand-name {
    font-family: "Montserrat", sans-serif; font-weight: 800;
    font-size: 52px; letter-spacing: 1px; color: var(--emboss);
  }

  /* front side */
  .front-brand {
    position: absolute; left: 30px; top: 66px;
    display: flex; align-items: center; gap: 12px;
  }
  .front-brand .brand-mark { width: 30px; height: 30px; border-radius: 50%; background: var(--sky); }
  .front-brand .brand-name {
    font-family: "Montserrat", sans-serif; font-weight: 800;
    font-size: 34px; letter-spacing: 0.5px; color: var(--white);
  }
  .person {
    position: absolute; right: 42px; top: 24px; text-align: right;
    font-family: "Montserrat", sans-serif; font-weight: 800;
  }
  .person-name { font-size: 25px; line-height: 1.1; }
  .person-name .first { color: var(--sky); }
  .person-name .last { color: var(--white); }
  .person-title { font-size: 15px; font-weight: 700; color: var(--white); margin-top: 4px; }

  .contact {
    position: absolute; left: 58px; top: 178px;
    font-family: "Open Sans", sans-serif; font-size: 13px; line-height: 1.35;
    color: var(--white);
  }
  .contact-address { margin-bottom: 8px; }
  .contact-list { list-style: none; }
  .contact-list li { display: flex; align-items: center; gap: 8px; }
  .contact-list svg { width: 12px; height: 12px; flex: none; }
</style>
</head>
<body>
<main class="stage">

  <section class="card card-back" aria-label="Card back">
    <div class="back-brand">
      <span class="brand-mark"></span>
      <span class="brand-name">VERODEX</span>
    </div>
  </section>

  <section class="card card-front" aria-label="Card front">
    <svg class="card-art" viewBox="0 0 540 310" aria-hidden="true">
      <defs>
        <linearGradient id="wave-fill" x1="0" y1="1" x2="1" y2="0">
          <stop offset="0" stop-color="#62c8dc"/>
          <stop offset="1" stop-color="#4a7cc4"/>
        </linearGradient>
        <linearGradient id="strip-fill" x1="0" y1="0" x2="0" y2="1">
          <stop offset="0" stop-color="#4a80c6"/>
          <stop offset="1" stop-color="#62c8dc"/>
        </linearGradient>
      </defs>
      <path d="M120 310 C 250 292, 340 240, 395 150 C 420 112, 460 98, 540 92 L540 310 Z" fill="url(#wave-fill)"/>
      <path d="M112 268 C 200 282, 300 262, 370 222 C 310 268, 220 292, 118 284 Z" fill="#ffffff"/>
      <rect x="516" y="0" width="24" height="48" fill="url(#strip-fill)"/>
      <circle cx="455" cy="188" r="52" fill="#5fb6e0" opacity="0.55"/>
    </svg>

    <div class="front-brand">
      <span class="brand-mark"></span>
      <span class="brand-name">VERODEX</span>
    </div>

    <div class="person">
      <div class="person-name"><span class="first">Lena</span> <span class="last">Marvik</span></div>
      <div class="person-title">Co-Founder</div>
    </div>

    <div class="contact">
      <p class="contact-address">740 Elmridge Ave. Suite 310<br>Dayton, OH 45402</p>
      <ul class="contact-list">
        <li>
          <svg viewBox="0 0 12 12"><path d="M2.5 1 L4.5 1 L5.3 3.4 L4 4.4 C4.6 5.8 6 7.2 7.6 8 L8.6 6.7 L11 7.5 L11 9.5 C11 10.4 10.3 11 9.4 11 C5 10.6 1.4 7 1 2.6 C1 1.7 1.6 1 2.5 1 Z" fill="#ffffff"/></svg>
          <span>(555) 214-0687</span>
        </li>
        <li>
          <svg viewBox="0 0 12 12"><rect x="1" y="2.5" width="10" height="7" rx="1" fill="none" stroke="#ffffff" stroke-width="1.2"/><path d="M1.5 3 L6 6.5 L10.5 3" fill="none" stroke="#ffffff" stroke-width="1.2"/></svg>
          <span>info@verodex.com</span>
        </li>
        <li>
          <svg viewBox="0 0 12 12"><circle cx="6" cy="6" r="5" fill="none" stroke="#ffffff" stroke-width="1.2"/><ellipse cx="6" cy="6" rx="2.2" ry="5" fill="none" stroke="#ffffff" stroke-width="1"/><path d="M1 6 H11" stroke="#ffffff" stroke-width="1"/></svg>
          <span>www.verodex.com</span>
        </li>
      </ul>
    </div>
  </section>

</main>
</body>
</html>
```